House flipping business web site needed

pinecrestholdingsgroup.example.
I am a residential developer in Northern NJ and I am looking for a fresh new updated website. I have an intro video about my company being made now. I don't update it very often but I want an easy format that I can add update photos to on projects I have worked on or homes I renovate for sale.

Target Market(s)

investors into my projects so a portfolio , people looking to sell their homes to me.

Industry/Entity Type

Real Estate Development

Number of Pages Required

4 page

Font styles to use
Serif

Colors
33b8a4
39a9d7
cadf82

Requirements
Must have
• space for an intro video about my company
• a portfolio with pictures and information about each project
• Markets we serve- Morris County, NJ
• My logo- already created
• SEO
• Yes I would like this to function over all platforms. Phone, computer, all platforms.
• history and background page
• I am looking for a completed page that I can upload to the site that hosts my website
Nice to have
• I want something creative, easy to navigate. modern.

```html
<!DOCTYPE html>
<html lang="en">
<head>
<meta charset="utf-8">
<title>Pinecrest Holdings Group</title>
<link rel="stylesheet" href="https://fonts.googleapis.com/css2?family=Mulish:wght@300;400;600;700&display=swap">
<style>
  :root {
    --teal: #33b8a4;
    --teal-deep: #22a285;
    --blue: #39a9d7;
    --lime: #cadf82;
    --paper: #f4f4f5;
    --ink: #4a4a4a;
    --muted: #9a9a9a;
    --night: #262626;
    --white: #ffffff;
  }
  * { margin: 0; padding: 0; box-sizing: border-box; }
  html, body { width: 1200px; height: 3169px; overflow: hidden; }
  body {
    position: relative;
    background: var(--paper);
    font-family: "Mulish", Arial, sans-serif;
    color: var(--ink);
  }
  .abs { position: absolute; }
  .center-text { left: 0; width: 1200px; text-align: center; }

  /* Hero */
  .hero { top: 0; left: 0; width: 1200px; height: 744px;
    background: linear-gradient(180deg, #3a4554 0%, #2d3540 45%, #3b3a38 75%, #2a2d33 100%); }
  .hero-shade { inset: 0; background: rgba(20, 26, 34, 0.25); }
  .header-curve { top: 0; left: 0; width: 1200px; height: 170px; }
  .nav-link { top: 70px; font-size: 14px; letter-spacing: 0.5px; color: #5a5a5a; text-decoration: none; }
  .nav-link.is-active::after { content: ""; position: absolute; left: -8px; right: -8px; top: 28px; height: 3px; background: var(--lime); }
  .brand { top: 36px; left: 450px; width: 300px; text-align: center; }
  .brand-mark { display: inline-block; width: 30px; height: 30px; border-radius: 50%; background: var(--blue); }
  .brand-name { display: block; margin-top: 4px; font-size: 22px; font-weight: 700; line-height: 1.05; color: var(--blue); letter-spacing: 1px; }
  .hero-title { top: 306px; font-size: 46px; font-weight: 300; color: var(--white); }
  .hero-sub { top: 374px; font-size: 18px; color: #e8e8e8; }
  .btn { display: flex; align-items: center; justify-content: center; font-size: 13px; letter-spacing: 0.6px; text-transform: uppercase; color: var(--white); }
  .btn-blue { top: 431px; left: 490px; width: 220px; height: 46px; background: var(--blue); font-size: 14px; }
  .slider-dots { top: 664px; left: 560px; width: 80px; display: flex; justify-content: space-between; }
  .slider-dots span { width: 9px; height: 9px; border-radius: 50%; background: var(--white); }
  .slider-dots span.is-current { background: var(--blue); }

  /* Section titles */
  .section-title { font-size: 28px; letter-spacing: 1px; }
  .title-rule { left: 539px; width: 122px; height: 5px; background: var(--lime); }

  /* Intro */
  .intro-title { top: 820px; color: var(--blue); }
  .video-frame { top: 925px; left: 270px; width: 655px; height: 334px; background: var(--white); padding: 5px; box-shadow: 0 3px 6px rgba(0,0,0,0.12); }
  .video-still { width: 100%; height: 100%; background: linear-gradient(180deg, #d9d9d9 0%, #c2c2c2 55%, #9e9e9e 100%); position: relative; }
  .play-button { position: absolute; left: 278px; top: 118px; width: 88px; height: 88px; }

  /* Portfolio */
  .portfolio { top: 1337px; left: 0; width: 1200px; height: 658px;
    background: linear-gradient(180deg, #6a3c26 0%, #8a4f2b 35%, #6e3b1f 70%, #4b2714 100%); }
  .portfolio-title { top: 1397px; color: var(--white); }
  .project-card { top: 1528px; width: 258px; height: 359px; background: var(--white); box-shadow: 0 3px 8px rgba(0,0,0,0.3); text-align: center; }
  .project-photo { margin: 9px 9px 0; height: 184px; background: linear-gradient(180deg, #9fb6c4 0%, #b7b9b0 45%, #6f8c4a 100%); }
  .project-town { margin-top: 20px; font-size: 17px; color: var(--blue); }
  .project-desc { margin: 14px 18px 0; font-size: 9.5px; line-height: 1.55; color: var(--muted); }
  .btn-teal { margin: 13px auto 0; width: 93px; height: 28px; background: var(--teal); font-size: 10px; }

  /* Help */
  .help { top: 1995px; left: 0; width: 1200px; height: 431px; background: var(--teal-deep); }
  .help-title { top: 2070px; color: var(--white); }
  .help-text { top: 2194px; left: 160px; width: 880px; text-align: center; font-size: 17px; line-height: 1.95; color: #eef7f4; }
  .btn-lime { top: 2297px; left: 490px; width: 220px; height: 49px; background: var(--lime); }

  /* Markets */
  .markets { top: 2426px; left: 0; width: 1200px; height: 505px;
    background: linear-gradient(180deg, #2e2e2e 0%, #3b3b3b 50%, #1f1f1f 100%); }
  .markets-title { top: 2481px; color: var(--white); }
  .county-map { top: 2553px; left: 194px; width: 328px; height: 314px; }
  .county-label { top: 2682px; left: 300px; width: 160px; text-align: center; color: var(--white); }
  .county-label b { display: block; font-size: 17px; font-weight: 600; }
  .county-label small { font-size: 9px; letter-spacing: 0.5px; }
  .contact-icon { width: 24px; height: 24px; }
  .contact-line { left: 590px; font-size: 27px; font-weight: 300; color: var(--white); line-height: 1.3; }

  /* Footer */
  .footer-brand { top: 2979px; left: 450px; width: 300px; text-align: center; }
  .footer-brand .brand-name { color: #6d6d6d; font-size: 20px; }
  .footer-brand .brand-mark { background: #8a8a8a; width: 26px; height: 26px; }
  .footer-nav { top: 3087px; font-size: 12px; color: #333; letter-spacing: 0.4px; }
  .footer-nav span { margin: 0 12px; }
  .copyright { top: 3118px; font-size: 10px; color: #555; letter-spacing: 0.4px; }
</style>
</head>
<body>

  <!-- Hero -->
  <section class="abs hero" role="img" aria-label="Waterfront city skyline at dusk"></section>
  <div class="abs hero-shade"></div>

  <svg class="abs header-curve" viewBox="0 0 1200 170" aria-hidden="true">
    <path d="M0 88 Q600 198 1200 88 V104 Q600 206 0 104 Z" fill="var(--blue)"/>
    <path d="M0 0 H1200 V80 Q600 190 0 80 Z" fill="var(--white)"/>
  </svg>

  <a class="abs nav-link is-active" style="left:317px">HOME</a>
  <a class="abs nav-link" style="left:407px">ABOUT</a>
  <a class="abs nav-link" style="left:693px">CONTACT</a>
  <a class="abs nav-link" style="left:806px">PORTFOLIO</a>

  <div class="abs brand">
    <span class="brand-mark"></span>
    <span class="brand-name">PINECREST<br>HOLDINGS</span>
  </div>

  <h1 class="abs center-text hero-title">Pinecrest Holdings Group</h1>
  <p class="abs center-text hero-sub">Investing in our neighborhoods</p>
  <a class="abs btn btn-blue">Get Started</a>
  <div class="abs slider-dots"><span class="is-current"></span><span></span><span></span><span></span></div>

  <!-- Intro -->
  <h2 class="abs center-text section-title intro-title">INTRO</h2>
  <div class="abs title-rule" style="top:870px"></div>
  <div class="abs video-frame">
    <div class="video-still" role="img" aria-label="Intro video still: a tree growing from stacks of coins">
      <svg class="play-button" viewBox="0 0 88 88" aria-hidden="true">
        <circle cx="44" cy="44" r="40" fill="rgba(255,255,255,0.25)" stroke="#ffffff" stroke-width="4"/>
        <path d="M34 24 L64 44 L34 64 Z" fill="var(--blue)"/>
      </svg>
    </div>
  </div>

  <!-- Portfolio -->
  <section class="abs portfolio" role="img" aria-label="Renovated kitchen with wooden cabinets"></section>
  <h2 class="abs center-text section-title portfolio-title">PORTFOLIO</h2>
  <div class="abs title-rule" style="top:1444px"></div>

  <article class="abs project-card" style="left:199px">
    <div class="project-photo" role="img" aria-label="Renovated two-storey house"></div>
    <h3 class="project-town" style="font-weight:400">Rockaway, NJ</h3>
    <p class="project-desc">Many upgrades to this home. Added a new full bath, family room, office, kitchenette and kids play room in walk out basement</p>
    <a class="btn btn-teal">View Details</a>
  </article>
  <article class="abs project-card" style="left:473px">
    <div class="project-photo" role="img" aria-label="Renovated gray colonial house"></div>
    <h3 class="project-town" style="font-weight:400">Rockaway, NJ</h3>
    <p class="project-desc">Many upgrades to this home. Added a new full bath, family room, office, kitchenette and kids play room in walk out basement</p>
    <a class="btn btn-teal">View Details</a>
  </article>
  <article class="abs project-card" style="left:746px">
    <div class="project-photo" role="img" aria-label="Small blue cottage among trees"></div>
    <h3 class="project-town" style="font-weight:400">Rockaway, NJ</h3>
    <p class="project-desc">Many upgrades to this home. Added a new full bath, family room, office, kitchenette and kids play room in walk out basement</p>
    <a class="btn btn-teal">View Details</a>
  </article>

  <!-- Help -->
  <section class="abs help"></section>
  <h2 class="abs center-text section-title help-title">HOW CAN WE HELP</h2>
  <div class="abs title-rule" style="top:2124px"></div>
  <p class="abs help-text">Do you need to sell your home fast to avoid foreclosure, have estate home you do not want to fix to put on the market, moving for &nbsp;a job and need your house sold fast. We can help.</p>
  <a class="abs btn btn-lime">Contact Us</a>

  <!-- Markets -->
  <section class="abs markets" role="img" aria-label="House among trees in black and white"></section>
  <h2 class="abs center-text section-title markets-title">MARKETS WE SERVE</h2>
  <div class="abs title-rule" style="top:2532px"></div>
  <div class="abs county-map" role="img" aria-label="Map of Morris County, New Jersey" style="background:var(--blue);border-radius:38% 46% 40% 52%;box-shadow:0 6px 10px rgba(0,0,0,0.35)"></div>
  <div class="abs county-label"><b>Morris County</b><small>NEW JERSEY</small></div>

  <svg class="abs contact-icon" style="left:545px;top:2680px" viewBox="0 0 24 24" aria-hidden="true">
    <rect x="3" y="2" width="18" height="20" fill="none" stroke="var(--lime)" stroke-width="2.5"/>
    <rect x="8" y="7" width="8" height="6" fill="var(--lime)"/>
    <rect x="9" y="15" width="6" height="7" fill="var(--lime)"/>
  </svg>
  <p class="abs contact-line" style="top:2652px">Pinecrest Holdings Group<br>Morris County, NJ</p>

  <svg class="abs contact-icon" style="left:545px;top:2769px" viewBox="0 0 24 24" aria-hidden="true">
    <path d="M6.6 10.8c1.4 2.8 3.8 5.1 6.6 6.6l2.2-2.2c.3-.3.7-.4 1-.2 1.1.4 2.3.6 3.6.6.6 0 1 .4 1 1V20c0 .6-.4 1-1 1C10.6 21 3 13.4 3 4c0-.6.4-1 1-1h3.5c.6 0 1 .4 1 1 0 1.3.2 2.5.6 3.6.1.3 0 .7-.2 1L6.6 10.8z" fill="var(--lime)"/>
  </svg>
  <p class="abs contact-line" style="top:2762px">555-014-PINE (7463)</p>

  <!-- Footer -->
  <div class="abs footer-brand">
    <span class="brand-mark"></span>
    <span class="brand-name">PINECREST<br>HOLDINGS</span>
  </div>
  <nav class="abs center-text footer-nav">HOME<span>|</span>ABOUT<span>|</span>CONTACT<span>|</span>PORTFOLIO</nav>
  <p class="abs center-text copyright">COPYRIGHT 2016 &nbsp;ALL RIGHTS RESERVED</p>

</body>
</html>
```